Holistic Psychology clinic flyer-

We need a 3 fold flyer that is both professional and zen looking with holistic elements- bilingual on both sides.
I am looking for a design that conveys the sense of confidence, yet relaxing to the eye and makes people want to pick it up and read it!
We are all about balance (yin, yang) and bringing equilibrium to a person in their quest to get better.

Target Market(s)

families adults, teens children experiencing mental health issues

Industry/Entity Type

Psychologist

Font styles to use
Serif

Colors
fbf289
cee9f5
0455a3

Requirements
Must have
• my logo (spiral) ; French one side; English on the other. Text is provided; Some color but clean, zen elements
• Easy to read text
Nice to have
• nature elements, bamboo? trees etc. sunrise or sunset?
• The sunset back ground provided in the picture is not necessary
• families?
Should not have
• too many distracting elements; not too many colors. colors must be subtle and must flow together

```html
<!DOCTYPE html>
<html lang="fr">
<head>
<meta charset="utf-8">
<title>Clinique Harmonia – Dépliant</title>
<link href="https://fonts.googleapis.com/css2?family=Libre+Baskerville:wght@400;700&family=Crimson+Text:wght@400;600;700&display=swap" rel="stylesheet">
<style>
  :root{
    --navy:#22215e;
    --ink:#1b1b1b;
    --white:#ffffff;
    --sun-yellow:#fbf289;
    --sky-top:#2b5fb3;
    --sea-deep:#0455a3;
    --mist:#cee9f5;
  }
  html,body{margin:0;padding:0;width:1200px;height:848px;overflow:hidden;background:#fff;}
  .flyer{position:relative;width:1200px;height:848px;overflow:hidden;font-family:"Crimson Text",Georgia,serif;color:var(--ink);}
  .backdrop{position:absolute;inset:0;background:linear-gradient(to bottom,#2b5fb3 0%,#6f98cf 13%,#efe0a6 30%,#f7c75a 50%,#f5b13a 64%,#f9dc8c 66%,#eef4e6 76%,#a8c9e8 82%,#3f78c4 92%,#1a4ea0 100%);}
  .sunset-scene{position:absolute;left:800px;top:330px;width:400px;height:215px;background:linear-gradient(to bottom,rgba(251,242,137,0) 0%,rgba(251,242,137,.55) 55%,rgba(255,251,232,.85) 100%);}
  .panel{position:absolute;top:0;height:848px;}
  .panel--services{left:36px;width:332px;}
  .panel--welcome{left:434px;width:330px;}
  .panel--cover{left:800px;width:400px;text-align:center;}
  .panel-title{font-family:"Libre Baskerville",Georgia,serif;font-weight:700;color:var(--white);font-size:22px;line-height:27px;margin:0;position:absolute;left:0;white-space:nowrap;}
  .service{position:absolute;left:0;width:332px;}
  .service h3{font-family:"Libre Baskerville",Georgia,serif;font-size:13px;font-weight:700;margin:0;line-height:16.5px;}
  .service p,.body-text{margin:0;font-size:15.2px;line-height:16.5px;text-align:justify;}
  .body-text{position:absolute;left:0;width:330px;}
  .tagline{position:absolute;left:0;width:330px;text-align:center;font-family:"Libre Baskerville",Georgia,serif;font-weight:700;font-size:17.5px;line-height:22px;margin:0;}
  .invite{position:absolute;left:0;width:330px;text-align:center;font-size:20px;line-height:22px;margin:0;}
  .contact-line{position:absolute;left:62px;display:flex;align-items:center;gap:12px;margin:0;}
  .contact-line svg{flex:none}
  .contact-line--phone{top:766px;font-family:"Libre Baskerville",Georgia,serif;font-weight:700;font-size:23px;}
  .contact-line--mail{top:800px;font-size:21px;}
  .brand{position:absolute;left:0;width:400px;top:84px;display:flex;justify-content:center;align-items:center;gap:12px;}
  .brand-name{font-family:"Libre Baskerville",Georgia,serif;font-size:54px;font-weight:400;color:var(--navy);}
  .brand-dot{width:26px;height:26px;border-radius:50%;background:var(--sun-yellow);}
  .clinic-name{position:absolute;left:0;width:400px;top:228px;margin:0;font-family:"Libre Baskerville",Georgia,serif;font-weight:700;font-size:31px;color:var(--navy);white-space:nowrap;}
  .cover-sub,.audience{position:absolute;left:0;width:400px;margin:0;font-family:"Libre Baskerville",Georgia,serif;font-weight:700;font-size:16.5px;line-height:20.5px;}
  .cover-sub{top:284px;}
  .audience{top:568px;}
  .address{position:absolute;left:0;width:400px;top:682px;margin:0;font-family:"Libre Baskerville",Georgia,serif;font-weight:700;font-size:14.5px;line-height:20px;}
  .address .tel{font-size:17px;}
  .web-band{position:absolute;left:0;top:798px;width:400px;height:28px;background:var(--sun-yellow);font-size:18px;letter-spacing:9px;line-height:28px;}
</style>
</head>
<body>
<div class="flyer">
  <div class="backdrop"></div>
  <div class="sunset-scene" role="img" aria-label="Illustration d'un soleil couchant avec halo et oiseaux en vol au-dessus de la mer"></div>

  <section class="panel panel--services">
    <h2 class="panel-title" style="top:48px">Nos Services Psychologiques</h2>
    <div class="service" style="top:100px">
      <h3>Psychologie clinique</h3>
      <p>Les psychologues se spécialisent dans l’art de comprendre les gens. Venez apprendre à mieux vous connaître, ainsi que les gens qui font partie de votre vie. Venez régler les troubles émotifs et relationnels qui vous drainent. C’est le temps d’un changement!</p>
    </div>
    <div class="service" style="top:214px">
      <h3>Psychothérapie holistique</h3>
      <p>Nous adoptons les meilleures approches en psychologie pour vous aider à apaiser votre âme, équilibrer votre corps, et libérer votre esprit. Venez découvrir comment votre corps et votre esprit sont inter-reliés et quoi faire pour les harmoniser.</p>
    </div>
    <div class="service" style="top:329px">
      <h3>Coaching holistique</h3>
      <p>Les défis de la vie vous offrent également l’opportunité d’évoluer. Nos coachs holistiques s’avèrent passionnés et détiennent les compétences requises pour vous appuyer dans votre cheminement. Venez nous visiter, il est temps pour vous de découvrir votre potentiel!</p>
    </div>
    <div class="service" style="top:444px">
      <h3>Psychologie sportive</h3>
      <p>Le monde de la compétition et du sport est rempli de défis auquel un psychologue sportif peut s’avérer très utile. Enlevez vos blocages mentaux, augmentez votre performance, assurez votre réussite, Osez et visez haut!</p>
    </div>
    <div class="service" style="top:542px">
      <h3>Les évaluations psycho-éducationnelles</h3>
      <p>A l’aide des tests psychométriques nous vous aiderons à découvrir comment fonctionne votre cerveau ou de celui de votre enfant. Nous soulignerons les forces et comment remédier aux faiblesses. Un rapport détaillé et un plan d’intervention académique est conçu pour chaque individu de 4 à 64 ans.</p>
    </div>
    <div class="service" style="top:674px">
      <h3>Cours de meditation pleine conscience</h3>
      <p>La méditation est reconnue comme bien plus qu’une technique pour entraîner la paix intérieure. Elle vous amène vers une nouvelle philosophie de vie saine et enrichie. Ces cours sont offerts de façon hebdomadaire et vous seront utiles pour vous enseigner comment méditer, et comment l’intégrer à votre quotidien.</p>
    </div>
  </section>

  <section class="panel panel--welcome">
    <h2 class="panel-title" style="top:48px">Bienvenue à la<br>Clinique Harmonia</h2>
    <p class="body-text" style="top:124px">Nous vous présentons une toute nouvelle manière de réaliser le bien-être que vous désirez atteindre dans votre vie. Nous vous offrons une variété de services, à la fois cliniques et éducatifs, dans un environnement professionnel et convivial. Nous utilisons une approche intégrative.</p>
    <p class="body-text" style="top:244px">Nous sommes passionnés à vous soutenir à atteindre votre potentiel et retrouvez votre bien-être en adoptant une approche qui intègre pensée, corps et esprit. Il est temps de penser à vous…</p>
    <p class="tagline" style="top:364px">Calmez vos pensées,<br>Détendez votre corps,<br>Stimulez votre esprit.</p>
    <p class="body-text" style="top:482px">Mathieu Delorme, BSc, MA. est le fondateur et directeur d’Harmonia. Il est psychologue, auteur et conférencier avec plus de 26 ans d’expérience. Mathieu est un pionnier dans le domaine de la psychologie holistique, une approche intégrative qui promouvoit la santé optimale et le bien-être. Mathieu et son équipe sont en mesure de vous aider avec tout vos défis personnels!</p>
    <p class="invite" style="top:682px">Rejoignez-nous pour une<br>consultation gratuite!</p>
    <p class="contact-line contact-line--phone">
      <svg width="16" height="16" viewBox="0 0 16 16" aria-hidden="true"><rect width="16" height="16" rx="3" fill="#1b1b1b"/><path d="M5 3.5c-.8.4-1.2 1.3-.9 2.4.6 2.4 2.6 4.6 5 5.5 1 .4 1.9 0 2.4-.8l-1.7-1.4-1 .7C7.7 9.3 6.8 8.4 6.3 7.3l.7-1z" fill="#fff"/></svg>
      514-555-0147
    </p>
    <p class="contact-line contact-line--mail">
      <svg width="16" height="14" viewBox="0 0 16 14" aria-hidden="true"><rect width="16" height="14" rx="2" fill="#1b1b1b"/><path d="M2 4l6 4 6-4" stroke="#fff" stroke-width="1.4" fill="none"/></svg>
      info@harmoniapsy.com
    </p>
  </section>

  <section class="panel panel--cover">
    <div class="brand"><span class="brand-dot"></span><span class="brand-name">Harmonia</span></div>
    <h1 class="clinic-name">Clinique Harmonia</h1>
    <p class="cover-sub">Psychologues<br>et<br>Professionnels de<br>l'éducation<br>avec une approche<br>intégrative</p>
    <p class="audience">Enfants<br>Adolescents<br>Adultes<br>Couples</p>
    <p class="address">4580 Boul. des Érables, Laval,<br>Québec H7T 2K9<br><span class="tel">Tel: (514) 555-0147</span><br>info@harmoniapsy.com<br>www.facebook.com/HarmoniaPsy</p>
    <div class="web-band">www.harmoniapsy.com</div>
  </section>
</div>
</body>
</html>
```